Modern Verdell Tree Care Website

I need a website for a full service Tree Care company. The company provides tree pruning, tree removal, tree preservation, emergency services, stump grinding, and emergency tree services.

Target Market(s)

Customers that need tree services

Industry/Entity Type

Landscaping, Tree Services

Coding

Coded - Design and coding required

Number of Pages Required

5+ page

Font styles to use
Sans Serif

Requirements
Must have
• Good clean design that showcases the services the company provides.
Nice to have
• Services page; contact form, blog, home page, about page

```html
<!DOCTYPE html>
<html lang="en">
<head>
<meta charset="utf-8">
<title>Verdell Tree Care</title>
<link href="https://fonts.googleapis.com/css2?family=Oswald:wght@500;600&family=Poppins:wght@400;500;600&display=swap" rel="stylesheet">
<style>
:root{
  --lime:#7fc241;
  --lime-dark:#6aab30;
  --forest:#2f4a27;
  --forest-deep:#233a1d;
  --ink:#111;
  --text:#222;
  --muted:#444;
  --orange:#f7a531;
  --white:#fff;
  --mist:#cfe3c3;
}
*{margin:0;padding:0;box-sizing:border-box}
html,body{width:1200px;height:3148px;overflow:hidden}
body{position:relative;font-family:'Poppins',sans-serif;color:var(--text);background:var(--white)}
.abs{position:absolute}
.display{font-family:'Oswald',sans-serif;font-weight:600;color:var(--ink);line-height:1.12}
.accent{color:var(--lime)}
.btn{position:absolute;background:var(--lime);color:var(--white);font-size:13px;display:flex;align-items:center;justify-content:center;border-radius:2px}

/* hero */
.hero-bg{left:0;top:0;width:1200px;height:680px;background:linear-gradient(180deg,#bcd9b0 0%,#c9e0bd 45%,#e6f0e0 75%,#fff 100%)}
.hero-tree{left:575px;top:70px;width:615px;height:500px;border-radius:48% 52% 20% 20%/55% 55% 20% 20%;background:radial-gradient(ellipse at 50% 35%,#5d9a3e 0%,#79ad58 45%,rgba(188,217,176,0) 72%)}
.logo{left:92px;top:26px;display:flex;align-items:center;gap:10px}
.logo-mark{width:28px;height:28px;background:var(--lime)}
.logo-name{font-family:'Poppins',sans-serif;font-weight:600;font-size:17px;color:#555;letter-spacing:.5px;line-height:1.05;width:110px}
.nav{left:404px;top:31px;display:flex;gap:34px;font-size:13.5px;color:#222}
.nav .active{font-weight:600}
.hero-title{left:92px;top:176px;font-size:44px}
.hero-copy{left:92px;top:285px;width:460px;font-size:13.5px;line-height:1.6}

/* about */
.eyebrow{font-size:19px;color:#222}
.about-copy{left:92px;top:833px;width:475px;font-size:12.2px;line-height:1.65;text-align:justify}
.about-copy p+p{margin-top:10px}
.photo{border-radius:6px}

/* dark band */
.dark-band{left:0;top:1180px;width:1200px;height:1150px;background:linear-gradient(180deg,rgba(47,74,39,0) 0%,var(--forest) 9%,var(--forest) 30%,var(--forest-deep) 70%,var(--forest-deep) 88%,rgba(35,58,29,0) 100%)}
.light{color:var(--white)}
.center{text-align:center;width:1200px;left:0}
.service{width:160px;text-align:center;top:1532px}
.ring{width:112px;height:112px;margin:0 auto;border-radius:50%;border:6px solid var(--lime);border-left-color:transparent;padding:6px}
.ring span{display:block;width:100%;height:100%;border-radius:50%;border:2px solid #fff}
.service h3{font-family:'Oswald',sans-serif;font-weight:500;font-size:14.5px;color:#fff;margin-top:16px}
.service p{font-size:10px;color:#dfe9d8;line-height:1.5;margin-top:4px}
.em-copy{left:633px;top:1975px;width:475px;font-size:12.2px;line-height:1.7;color:#eef3ea;text-align:justify}
.thumb{top:2148px;width:153px;height:90px;border-radius:3px}

/* why */
.feature{width:240px;text-align:center}
.icon-box{width:54px;height:54px;margin:0 auto;background:var(--orange);border-radius:3px;display:flex;align-items:center;justify-content:center}
.feature h3{font-family:'Oswald',sans-serif;font-weight:500;font-size:15px;color:var(--ink);margin-top:16px}
.feature p{font-size:10px;color:var(--muted);line-height:1.5;margin-top:3px}

/* footer */
.footer{left:0;top:2822px;width:1200px;height:326px;background:linear-gradient(180deg,#36563a 0%,#2e4c31 50%,#264128 100%)}
.footer .logo-name{color:#fff}
.footer .logo-mark{background:#fff}
.f-copy{font-size:10.5px;line-height:1.6;color:#e8efe4;text-align:justify}
.f-head{font-size:13px;font-weight:600;color:#fff}
.f-list{font-size:10.5px;color:#e8efe4;line-height:1.85;list-style:none}
.social{display:flex;gap:6px}
.social span{width:25px;height:25px;border-radius:50%;background:var(--lime)}
.input{background:#fff;border-radius:2px;font-size:10px;color:#888;padding-left:16px;display:flex;align-items:center}
</style>
</head>
<body>

<!-- HERO -->
<div class="abs hero-bg"></div>
<div class="abs hero-tree" role="img" aria-label="Large green tree standing in a misty meadow"></div>
<div class="abs logo"><span class="logo-mark"></span><span class="logo-name">VERDELL TREE CARE</span></div>
<nav class="abs nav"><span class="active">Home</span><span>Services</span><span>Blog</span><span>About us</span><span>Contact us</span></nav>
<div class="btn" style="left:984px;top:21px;width:124px;height:37px;font-size:13.5px">Get started</div>
<h1 class="abs display hero-title">Expert Tree Care Services<br>for Your Home and Business</h1>
<p class="abs hero-copy">Our team of licensed arborists is dedicated to providing top-notch service with a focus on safety and customer satisfaction.</p>
<div class="btn" style="left:92px;top:352px;width:170px;height:38px;font-size:13.5px">Get a free estimate</div>

<!-- ABOUT -->
<p class="abs eyebrow" style="left:92px;top:693px">Who We Are</p>
<h2 class="abs display" style="left:92px;top:726px;font-size:43px">Your <span class="accent">Trusted</span> Tree Care<br>Experts</h2>
<div class="abs about-copy">
<p>At Verdell Tree Care, we are more than just a tree service company; we are stewards of our beautiful trees. With a passion deeply rooted in arboriculture, we embark on a mission to promote the health, beauty, and safety of your trees and landscapes.</p>
<p>Whether it's expert tree trimming to enhance aesthetics, meticulous tree removal to mitigate hazards, or comprehensive tree health assessments to ensure safety, we approach each task with unwavering dedication and attention to detail.</p>
</div>
<div class="btn" style="left:92px;top:1007px;width:108px;height:36px;font-size:12px">Learn more</div>

<div class="abs photo" style="left:655px;top:708px;width:453px;height:575px;background:var(--lime)"></div>
<div class="abs photo" role="img" aria-label="Arborist climbing a tree trunk with safety ropes among green leaves" style="left:632px;top:683px;width:451px;height:575px;background:linear-gradient(160deg,#9bc27a 0%,#5e7e45 45%,#3d4f2e 100%)"></div>

<div class="dark-band abs"></div>

<div class="abs photo" style="left:320px;top:1050px;width:423px;height:288px;background:var(--lime)"></div>
<div class="abs photo" role="img" aria-label="Climber working high in a tree against a cloudy sky" style="left:346px;top:1026px;width:422px;height:287px;background:linear-gradient(110deg,#d9dde0 0%,#bfc6cb 50%,#6b6f5e 80%,#3a3d30 100%)"></div>

<!-- SERVICES -->
<p class="abs eyebrow center light" style="top:1414px">Our Services</p>
<h2 class="abs display center light" style="top:1446px;font-size:43px;color:#fff"><span class="accent">Comprehensive</span> Tree Care Solutions</h2>

<div class="abs service" style="left:88px"><div class="ring"><span role="img" aria-label="Worker trimming tree branches" style="background:#8a6a4c"></span></div><h3>Tree Trimming</h3><p>Enhance the aesthetics and health of your trees with our expert trimming services.</p></div>
<div class="abs service" style="left:260px"><div class="ring"><span role="img" aria-label="Worker removing a large tree" style="background:#9a8c7c"></span></div><h3>Tree Removal</h3><p>Safe and efficient tree removal to protect your property.</p></div>
<div class="abs service" style="left:433px"><div class="ring"><span role="img" aria-label="Hands holding a young seedling in soil" style="background:#4e3a2c"></span></div><h3>Tree Preservation</h3><p>Specialized techniques to ensure the longevity and health of your trees.</p></div>
<div class="abs service" style="left:606px"><div class="ring"><span role="img" aria-label="Fallen tree after a storm" style="background:#7ca25c"></span></div><h3>Emergency Tree Services</h3><p>Rapid response to storm damage and other emergencies.</p></div>
<div class="abs service" style="left:779px"><div class="ring"><span role="img" aria-label="Stump grinding machine at work" style="background:#b8772f"></span></div><h3>Stump Grinding</h3><p>Complete removal of stumps to maintain a clean and safe landscape.</p></div>
<div class="abs service" style="left:952px"><div class="ring"><span role="img" aria-label="Tree supported with cables and braces" style="background:#8db7d8"></span></div><h3>Cabling &amp; Bracing</h3><p>Support for weakened trees to prevent potential hazards.</p></div>

<!-- EMERGENCY -->
<div class="abs photo" role="img" aria-label="Utility bucket truck clearing fallen trees on a street" style="left:92px;top:1803px;width:474px;height:469px;background:linear-gradient(170deg,#6f8a5a 0%,#8f9c8a 45%,#c9ccc8 70%,#4d5a3f 100%)"></div>
<p class="abs eyebrow light" style="left:633px;top:1836px">24/7 Emergency Services</p>
<h2 class="abs display" style="left:633px;top:1869px;font-size:43px;color:#fff"><span class="accent">Immediate</span> Response for<br>Tree Emergencies</h2>
<p class="abs em-copy">When disaster strikes, Verdell Tree Care is here to help. Our 24-hour emergency services are designed to provide quick and efficient solutions to any tree-related emergencies. From storm damage cleanup to hazardous tree removal, we are ready to respond at any time.</p>
<div class="btn" style="left:633px;top:2083px;width:134px;height:37px;font-size:12px">Contact us now</div>
<div class="abs thumb" role="img" aria-label="Car crushed by a fallen tree" style="left:633px;background:linear-gradient(135deg,#5d7a45,#9b3a3a 60%,#6c6f5c)"></div>
<div class="abs thumb" role="img" aria-label="Storm debris scattered across a yard" style="left:794px;background:linear-gradient(135deg,#6f7d4e,#8a9068)"></div>
<div class="abs thumb" role="img" aria-label="Tree branches fallen on a parked car" style="left:955px;background:linear-gradient(135deg,#3f6a2e,#b9bdc0)"></div>

<!-- WHY -->
<p class="abs eyebrow center" style="top:2348px">Why Choose Us</p>
<h2 class="abs display center" style="top:2380px;font-size:43px"><span class="accent">Quality</span> Service You Can Trust</h2>

<div class="abs feature" style="left:80px;top:2460px"><div class="icon-box"><svg width="22" height="22" viewBox="0 0 24 24" fill="none" stroke="#fff" stroke-width="1.6"><rect x="3" y="4" width="18" height="14" rx="1"/><path d="M7 9h10M7 13h6"/></svg></div><h3>Licensed and Insured</h3><p>Ensuring compliance with industry standards and providing peace of mind.</p></div>
<div class="abs feature" style="left:347px;top:2460px"><div class="icon-box"><svg width="22" height="22" viewBox="0 0 24 24" fill="none" stroke="#fff" stroke-width="1.6"><path d="M6 18a6 6 0 0112 0M4 18h16M12 4v3M5 8l2 2M19 8l-2 2"/></svg></div><h3>24-Hours Emergency Services</h3><p>Available 24/7 to handle any tree-related emergencies promptly and effectively.</p></div>
<div class="abs feature" style="left:613px;top:2460px"><div class="icon-box"><svg width="22" height="22" viewBox="0 0 24 24" fill="none" stroke="#fff" stroke-width="1.6"><path d="M4 11l8-7 8 7v9H4z"/><path d="M10 20v-5h4v5"/></svg></div><h3>Locally Owned &amp; Operated</h3><p>Committed to serving and understanding our community's needs.</p></div>
<div class="abs feature" style="left:880px;top:2460px"><div class="icon-box"><svg width="22" height="22" viewBox="0 0 24 24" fill="none" stroke="#fff" stroke-width="1.6"><rect x="3" y="7" width="18" height="12" rx="1"/><path d="M9 7V5h6v2M3 12h18"/></svg></div><h3>Professional Work</h3><p>Performs all tasks with the utmost professionalism.</p></div>

<div class="abs feature" style="left:213px;top:2625px"><div class="icon-box"><svg width="22" height="22" viewBox="0 0 24 24" fill="none" stroke="#fff" stroke-width="1.6"><path d="M12 3l7 3v5c0 5-3 8-7 10-4-2-7-5-7-10V6z"/><path d="M9 12l2 2 4-4"/></svg></div><h3>Safety is Our No.1 Priority</h3><p>Follow stringent safety protocols to protect you, your property, and our workers.</p></div>
<div class="abs feature" style="left:480px;top:2625px"><div class="icon-box"><svg width="22" height="22" viewBox="0 0 24 24" fill="none" stroke="#fff" stroke-width="1.6"><path d="M9 4h6l-2 4h-2z"/><circle cx="12" cy="15" r="6"/></svg></div><h3>Free Estimates</h3><p>No-obligation estimates for all our services to provide transparent.</p></div>
<div class="abs feature" style="left:747px;top:2625px"><div class="icon-box"><svg width="22" height="22" viewBox="0 0 24 24" fill="none" stroke="#fff" stroke-width="1.6"><path d="M7 16a5 5 0 110-10 6 6 0 0111 2 4 4 0 01-1 8"/><path d="M12 11v9M9 14l3-3 3 3"/></svg></div><h3>Licensed Arborist on Staff</h3><p>Our team includes licensed arborists who ensure your trees receive expert care.</p></div>

<!-- FOOTER -->
<footer class="abs footer" role="img" aria-label="Misty pine forest backdrop"></footer>
<div class="abs logo" style="top:2856px"><span class="logo-mark"></span><span class="logo-name">VERDELL TREE CARE</span></div>
<p class="abs f-copy" style="left:92px;top:2900px;width:262px">Verdell Tree Care provides comprehensive tree services, including trimming, removal, preservation, and emergency response. With a team of licensed professionals, we ensure the health and beauty of your trees and landscapes.</p>
<p class="abs f-head" style="left:92px;top:3002px">Follow Us!</p>
<div class="abs social" style="left:92px;top:3030px"><span></span><span></span><span></span><span></span></div>

<p class="abs f-head" style="left:408px;top:2858px">Contact Information</p>
<ul class="abs f-list" style="left:408px;top:2880px"><li>(555) 014-2739</li><li>info@verdelltreecare.com</li><li>48 Maple Hollow Road, Brookfield, ST 00000</li></ul>
<p class="abs f-head" style="left:408px;top:2962px">Company</p>
<ul class="abs f-list" style="left:408px;top:2984px"><li>Support</li><li>Term &amp; Conditions</li><li>Privacy</li></ul>

<p class="abs f-head" style="left:655px;top:2858px">Quick Links</p>
<ul class="abs f-list" style="left:655px;top:2880px;line-height:1.8"><li>Home</li><li>About Us</li><li>Services</li><li>Emergency Services</li><li>Contact Us</li><li>Blog</li></ul>

<p class="abs f-head" style="left:813px;top:2858px">Newsletter</p>
<div class="abs input" style="left:813px;top:2887px;width:295px;height:31px">Write your email</div>
<div class="btn" style="left:813px;top:2924px;width:295px;height:31px;font-size:10.5px">Subscribe</div>

<div class="abs" style="left:92px;top:3093px;width:1016px;height:1px;background:rgba(255,255,255,.5)"></div>
<p class="abs center" style="top:3110px;font-size:10px;color:#e8efe4">© 2024 Verdell Tree Care. All rights reserved.</p>

</body>
</html>
```